Business card for Eyelash extension salon in Beverly Hills,California USA

We need new business card for our salon in Beverly Hills. The salon name is 'Lashvera' . We would like to have...Business name: Lashvera Name of person: will provide later Address 4720 N.Alder Crest Ave Beverly Hills , CA 90210 Phone: will provide later (Text only) Web: www.lashverastudio.example Snapgrid icon, Circlebook icon follow us for seasonal campaign and news @lashverastudiolounge Design should look elegant, high-end, clean, simple, cohesive with my brand. Please refer my brand board. Business name color will be metallic bronzy color. Im thinking grey background or white background. Thanks

Target Market(s)

25-35. Gender neutral. People who are in Entertainment business industry.
This is High-end Eyelash extension salon in Beverly Hills

Industry/Entity Type

Beauty Salon

Contact Information for Business Card

Business name: Lashvera
Name of person: will provide later
Address 4720 N.Alder Crest Ave Beverly Hills , CA 90210
Phone: will provide later (Text only)
Web: www.lashverastudio.example
Snapgrid icon, Circlebook icon
follow us for seasonal campaign and news @lashverastudiolounge

Requirements
Must have
• Beautiful, elegant, clean and simple look but very attractive and modern
Should not have
• We don't like too clutter, too busy designs.

```html
<!DOCTYPE html>
<html lang="en">
<head>
<meta charset="UTF-8">
<title>Lashvera Business Card</title>
<link href="https://fonts.googleapis.com/css2?family=Oswald:wght@500&family=Work+Sans:wght@300;400;500&display=swap" rel="stylesheet">
<style>
  :root {
    --backdrop: #2b2b2c;
    --card-black: #0a0a0b;
    --card-sheen: #1a1a1c;
    --bronze: #a77c5c;
    --bronze-deep: #8a6448;
    --ink-light: #e6e6e6;
    --ink-muted: #bdbdbd;
  }
  * { margin: 0; padding: 0; box-sizing: border-box; }
  html, body { width: 1200px; height: 800px; overflow: hidden; }
  body {
    background: var(--backdrop);
    font-family: "Work Sans", sans-serif;
    position: relative;
  }
  .card {
    position: absolute;
    width: 540px;
    height: 310px;
    border-radius: 18px;
    background: linear-gradient(115deg, var(--card-black) 0%, var(--card-black) 55%, var(--card-sheen) 66%, var(--card-black) 78%);
    box-shadow: 0 18px 40px rgba(0,0,0,0.45);
    overflow: hidden;
  }
  .card-front { left: 50px; top: 110px; }
  .card-back {
    left: 610px; top: 380px;
    border-bottom: 8px solid var(--bronze);
  }

  /* front */
  .brand {
    position: absolute;
    right: 70px; top: 92px;
    text-align: right;
  }
  .brand-name {
    font-size: 58px;
    font-weight: 300;
    color: var(--bronze);
    letter-spacing: 1px;
    line-height: 1;
  }
  .brand-place {
    margin-top: 8px;
    font-size: 9px;
    font-weight: 400;
    letter-spacing: 3px;
    text-transform: uppercase;
    color: var(--bronze);
  }
  .front-web {
    position: absolute;
    left: 48px; bottom: 44px;
    font-size: 15px;
    font-weight: 500;
    color: var(--bronze);
  }

  /* back */
  .accent-bar {
    position: absolute;
    right: 0; top: 40px;
    width: 10px; height: 70px;
    background: var(--bronze);
  }
  .person {
    position: absolute;
    right: 32px; top: 40px;
    text-align: right;
  }
  .person-name {
    font-family: "Oswald", sans-serif;
    font-weight: 500;
    font-size: 30px;
    color: var(--bronze);
    letter-spacing: 0.5px;
    line-height: 1.05;
  }
  .person-role {
    font-size: 13px;
    font-weight: 300;
    color: var(--ink-light);
    line-height: 1.5;
  }
  .contact {
    position: absolute;
    left: 40px; top: 140px;
    font-size: 14px;
    color: var(--ink-light);
    line-height: 1.45;
    font-weight: 300;
  }
  .contact-label { font-weight: 500; }
  .address {
    position: absolute;
    left: 40px; bottom: 62px;
    font-size: 14px;
    font-weight: 300;
    color: var(--ink-light);
  }
  .socials {
    position: absolute;
    left: 40px; bottom: 24px;
    display: flex;
    gap: 26px;
    font-size: 11px;
    color: var(--ink-muted);
  }
  .social { display: flex; align-items: center; gap: 7px; }
  .social-dot {
    width: 12px; height: 12px;
    border-radius: 50%;
    background: var(--bronze);
  }
</style>
</head>
<body>
  <section class="card card-front">
    <div class="brand">
      <div class="brand-name">Lashvera</div>
      <div class="brand-place">Beverly Hills</div>
    </div>
    <div class="front-web">www.lashverastudio.example</div>
  </section>

  <section class="card card-back">
    <div class="accent-bar"></div>
    <div class="person">
      <div class="person-name">DANIEL WHITCOMBE</div>
      <div class="person-role">Solicitor</div>
      <div class="person-role">Registered Migration Agent</div>
    </div>
    <div class="contact">
      <div><span class="contact-label">Phone:</span> 02 5550 0142</div>
      <div><span class="contact-label">Web:</span> www.lashverabh.example</div>
    </div>
    <div class="address">A : 4720 N.Alder Crest Ave Beverly Hills , CA 90210</div>
    <div class="socials">
      <span class="social"><span class="social-dot"></span>Snapgrid</span>
      <span class="social"><span class="social-dot"></span>Circlebook</span>
    </div>
  </section>
</body>
</html>
```